Accounting firm needing business card / letterhead designed
Marcus L. Trenholm, CPA
marcus@veltrowledger.com
www.veltrowledger.com
842 E Alder Ave Perrysburg, OH 43827
419-562-0974

```html
<!DOCTYPE html>
<html lang="en">
<head>
<meta charset="utf-8">
<title>Veltro Ledger – Business Card</title>
<link rel="stylesheet" href="https://fonts.googleapis.com/css2?family=Orbitron:wght@500;700&family=Roboto:wght@400&display=swap">
<style>
  :root {
    --stage: #1c1c1c;
    --navy: #272262;
    --navy-light: #4a3ca8;
    --green: #8dc63f;
    --paper-light: #f8f8f8;
    --paper-shade: #e8e8e8;
    --ink: #555555;
    --white: #ffffff;
  }
  * { margin: 0; padding: 0; box-sizing: border-box; }
  html, body { width: 1200px; height: 960px; overflow: hidden; }
  body { background: var(--stage); position: relative; font-family: "Roboto", sans-serif; }

  .card { position: absolute; width: 600px; height: 342px; }

  .card-front {
    left: 302px; top: 129px;
    background: linear-gradient(120deg, var(--paper-light) 0%, var(--paper-shade) 100%);
  }
  .edge-strip { position: absolute; right: 0; top: 0; width: 10px; height: 100%; }

  .brand-name {
    font-family: "Orbitron", sans-serif;
    font-weight: 700;
    letter-spacing: 2px;
    white-space: nowrap;
  }
  .card-front .brand-name {
    position: absolute; left: 34px; top: 46px;
    font-size: 40px; color: var(--navy);
  }

  .holder-name {
    position: absolute; right: 38px; top: 208px;
    font-family: "Orbitron", sans-serif; font-weight: 500;
    font-size: 21px; letter-spacing: 1px; color: var(--navy);
    text-transform: uppercase; white-space: nowrap;
  }
  .divider {
    position: absolute; left: 33px; right: 38px; top: 245px;
    height: 2px; background: var(--green);
  }

  .address {
    position: absolute; left: 31px; top: 278px;
    font-size: 14px; line-height: 19px; color: var(--ink);
  }
  .contact-list {
    position: absolute; right: 37px; top: 258px; list-style: none;
    font-size: 14px; line-height: 19px; color: var(--ink); text-align: right;
  }
  .contact-list li { display: flex; justify-content: flex-end; align-items: center; gap: 8px; }
  .contact-list svg { width: 13px; height: 13px; fill: var(--navy); flex: none; }

  .card-back {
    left: 299px; top: 488px;
    background: linear-gradient(135deg, var(--navy-light) 0%, #2f2778 35%, var(--navy) 70%);
    display: flex; align-items: center; justify-content: center;
  }
  .card-back .brand-name { font-size: 50px; color: var(--white); letter-spacing: 3px; }
</style>
</head>
<body>

<section class="card card-front" aria-label="Business card front">
  <svg class="edge-strip" viewBox="0 0 10 342" preserveAspectRatio="none" aria-hidden="true">
    <polygon points="0,0 10,0 10,112 0,118" fill="var(--green)"/>
    <polygon points="0,120 10,114 10,342 0,342" fill="var(--navy)"/>
  </svg>

  <div class="brand-name">VELTRO LEDGER</div>

  <h1 class="holder-name">Marcus L. Trenholm, CPA</h1>
  <div class="divider"></div>

  <address class="address">842 E Alder Ave<br>Perrysburg, OH 43827</address>

  <ul class="contact-list">
    <li>419-562-0974
      <svg viewBox="0 0 24 24" aria-hidden="true"><path d="M6.6 10.8a15.2 15.2 0 0 0 6.6 6.6l2.2-2.2a1 1 0 0 1 1-.25 11.4 11.4 0 0 0 3.6.57 1 1 0 0 1 1 1V20a1 1 0 0 1-1 1A17 17 0 0 1 3 4a1 1 0 0 1 1-1h3.5a1 1 0 0 1 1 1c0 1.25.2 2.45.57 3.57a1 1 0 0 1-.25 1z"/></svg>
    </li>
    <li>marcus@veltrowledger.com
      <svg viewBox="0 0 24 24" aria-hidden="true"><path d="M2 5h20v14H2z M3 6l9 7 9-7" stroke="var(--paper-light)" stroke-width="1.6"/></svg>
    </li>
    <li>www.veltrowledger.com
      <svg viewBox="0 0 24 24" aria-hidden="true"><circle cx="12" cy="12" r="11"/><path d="M2 12h20M12 1c4 4 4 18 0 22M12 1c-4 4-4 18 0 22" stroke="var(--paper-light)" stroke-width="1.4" fill="none"/></svg>
    </li>
  </ul>
</section>

<section class="card card-back" aria-label="Business card back">
  <div class="brand-name">VELTRO LEDGER</div>
</section>

</body>
</html>
```